Explosive, chemical reaction of creativity!

Web design for a digital marketing company. The unconventional is encouraged!
This is for a cool, young, geographically diverse company (sketchhive... you are all part of our team!!!)... we build websites but our real specialty is "search experience optimization".... creating conversion focused content, SEO (including content), and social media.

Target Market(s)

small to medium size businesses, law firms, medical practices, municipalities

Industry/Entity Type

Marketing

Number of Pages Required

2 page

Requirements
Must have
• WOW
• something different and special... we've been playing with a science theme (www.fernquillmedia.marketing) but we are open to different looks, layouts, etc.
• we nee a homepage design and an interior page design
• content needs to include: Marketing Catalysts (about us), Our Formula (services), Chemical Reactions(Results/Our Clients),
• FREE Online Prism Check
• Let us put together an objective snapshot of your digital presence for you.
Nice to have
• we are open to the use of background video (chemical reaction???)
• we are open to cool and different imagery
Should not have
• template look like most other websites

```html
<!DOCTYPE html>
<html lang="en">
<head>
<meta charset="utf-8">
<title>Fernquill Media — Search Experience Optimization</title>
<link href="https://fonts.googleapis.com/css2?family=Arimo:wght@400;700&family=Open+Sans:wght@400;600;700&display=swap" rel="stylesheet">
<style>
:root{
  --navy:#0f2340;
  --ink:#1c1c1c;
  --text:#6b6b6b;
  --blue:#1a64ae;
  --blue-deep:#0d3f7e;
  --blue-bright:#2a7fd0;
  --grey-band:#f0f0f0;
  --white:#ffffff;
  --green:#2fa847;
  --orange:#e07a2e;
  --yellow:#e2a915;
  --cyan:#1aa2d8;
  --coral:#ee5f5a;
  --footer:#ffffff;
}
*{box-sizing:border-box;margin:0;padding:0}
html,body{width:1200px;height:3136px;overflow:hidden}
body{font-family:"Open Sans",Arial,sans-serif;color:var(--text);background:var(--white);position:relative}
h1,h2,h3,h4,.nav a,.btn,.brand,.hero-title{font-family:"Arimo",Arial,sans-serif}
section,header,footer{position:absolute;left:0;width:1200px}
.abs{position:absolute}

/* header */
.site-header{top:0;height:88px;background:var(--white);border-top:5px solid var(--navy);box-shadow:0 1px 4px rgba(0,0,0,.08);z-index:2}
.brand{position:absolute;left:92px;top:26px;display:flex;align-items:center;gap:10px;font-weight:700;font-size:20px;letter-spacing:1px;color:var(--navy);white-space:nowrap}
.brand-mark{width:30px;height:30px;background:var(--navy)}
.nav{position:absolute;right:96px;top:34px;display:flex;gap:24px;align-items:center}
.nav a{font-size:13px;font-weight:700;color:var(--ink);text-decoration:none;white-space:nowrap}
.nav a.active{color:var(--blue)}

/* hero */
.hero{top:88px;height:399px;background:radial-gradient(ellipse at 55% 45%,#3a8fe6 0%,#14509e 40%,#07204a 80%,#041430 100%);text-align:center;color:var(--white)}
.hero .line1{position:absolute;top:134px;width:100%;font-size:32px;font-weight:700;letter-spacing:.5px}
.hero .line2{position:absolute;top:172px;width:100%;font-size:42px;font-weight:700}
.hero .arrow{position:absolute;top:180px}
.hero .down{position:absolute;left:580px;top:298px}

/* features */
.features{top:487px;height:193px;background:var(--grey-band)}
.feature{position:absolute;top:20px;width:240px;text-align:center}
.feature svg{display:block;margin:0 auto}
.feature h3{margin-top:14px;font-size:15px;color:var(--ink);letter-spacing:.3px}
.feature p{margin-top:6px;font-size:12px;line-height:18px;color:#888}

/* welcome */
.welcome{top:680px;height:501px}
.welcome h2{position:absolute;left:98px;top:50px;font-size:22px;color:var(--ink)}
.welcome .sub{position:absolute;left:98px;top:84px;font-size:16px;font-weight:600;color:var(--blue)}
.welcome .intro{position:absolute;left:98px;top:122px;width:720px;font-size:12px;line-height:24px}
.readmore{font-family:"Open Sans",Arial,sans-serif;font-weight:700;font-size:12px;color:var(--blue);text-decoration:none;white-space:nowrap}
.stat{position:absolute;width:320px;height:84px}
.stat .dot{position:absolute;left:0;top:0;width:82px;height:82px;border-radius:50%;display:flex;align-items:center;justify-content:center}
.stat .num{position:absolute;left:104px;top:0;font-family:"Arimo",Arial,sans-serif;font-weight:700;font-size:40px;color:var(--ink);line-height:44px}
.stat p{position:absolute;left:104px;top:48px;width:200px;font-size:12px;line-height:18px}
.phone-shot{position:absolute;left:853px;top:47px;width:328px;height:454px;border-radius:40px 40px 0 0;background:linear-gradient(160deg,#2b2b2b 0%,#4a4a4a 35%,#d9b8a0 70%,#e7c8ad 100%)}

/* facts */
.facts{top:1181px;height:311px;background:linear-gradient(135deg,#1f6fc0 0%,#1559a4 55%,#0f4a8f 100%);color:var(--white);text-align:center}
.facts h2{position:absolute;top:40px;width:100%;font-size:22px}
.facts .sub{position:absolute;top:76px;width:100%;font-size:16px;font-weight:600}
.fact{position:absolute;top:120px;width:220px;text-align:center}
.fact .ring{width:108px;height:108px;margin:0 auto;border:3px solid var(--white);border-radius:50%;display:flex;align-items:center;justify-content:center;font-family:"Arimo",Arial,sans-serif;font-weight:700;font-size:40px;background:rgba(255,255,255,.12)}
.fact p{margin-top:16px;font-size:12px;line-height:17px}

/* snapshot */
.snapshot{top:1492px;height:441px}
.snapshot h2{position:absolute;left:98px;top:74px;width:600px;font-size:21px;line-height:30px;color:var(--ink)}
.snapshot .copy{position:absolute;left:98px;top:158px;width:560px;font-size:12px;line-height:22px}
.snapshot .copy p+p{margin-top:14px}
.snapshot .readmore{position:absolute;left:98px;top:320px}
.cycle-label{position:absolute;font-family:"Arimo",Arial,sans-serif;font-size:13px;color:var(--ink);line-height:17px}

/* prism */
.prism{top:1933px;height:230px;background:linear-gradient(100deg,#8a5a2c 0%,#b58a55 30%,#6f88a0 60%,#2f5579 100%);text-align:center;color:var(--white)}
.prism h2{position:absolute;top:30px;width:100%;font-size:22px}
.prism p{position:absolute;top:68px;left:230px;width:740px;font-size:13.5px;line-height:24px}
.btn{position:absolute;left:494px;top:117px;width:213px;height:50px;border:2px solid var(--white);background:var(--blue);color:var(--white);font-weight:700;font-size:14px;display:flex;align-items:center;justify-content:center;text-decoration:none}

/* blog */
.blog{top:2163px;height:527px}
.blog h2{position:absolute;top:57px;width:100%;text-align:center;font-size:22px;color:var(--ink)}
.post{position:absolute;top:103px;width:314px}
.post .thumb{height:184px}
.post h3{margin-top:24px;font-size:13px;line-height:19px;color:var(--ink)}
.post .meta{margin-top:10px;font-size:12px;color:var(--blue)}
.post .excerpt{margin-top:10px;font-size:12px;line-height:20px}
.post .readmore{display:block;margin-top:12px}
.blog .side{position:absolute;top:185px}

/* contact */
.contact{top:2690px;height:376px;background:var(--navy);color:var(--white)}
.contact h2{position:absolute;top:38px;width:100%;text-align:center;font-size:22px}
.contact h4{position:absolute;top:86px;font-size:14px}
.field{position:absolute;height:32px;background:var(--white);color:#888;font-size:11px;padding:8px 12px}
.submit{position:absolute;left:625px;top:297px;width:103px;height:38px;border:2px solid var(--white);font-family:"Arimo",Arial,sans-serif;font-weight:700;font-size:12px;display:flex;align-items:center;justify-content:center}
.info{position:absolute;left:786px;display:flex;align-items:flex-start;gap:20px;font-size:12px;line-height:18px}
.info .ic{width:36px;height:36px;border:2px solid var(--white);border-radius:50%;display:flex;align-items:center;justify-content:center;flex:none}
.socials{position:absolute;left:786px;top:306px;display:flex;gap:12px}
.socials span{width:24px;height:24px;background:var(--white);border-radius:3px}

.site-footer{top:3066px;height:70px;background:var(--footer);text-align:center;font-size:12px;color:#888;padding-top:30px}
</style>
</head>
<body>

<header class="site-header">
  <div class="brand"><span class="brand-mark"></span>FERNQUILL MEDIA</div>
  <nav class="nav">
    <a class="active" href="#">HOME</a>
    <a href="#">MARKETING CATALYSTS</a>
    <a href="#">OUR FORMULA</a>
    <a href="#">CHEMICAL REACTIONS</a>
    <a href="#">CONTACT US</a>
    <svg width="16" height="16" viewBox="0 0 16 16" aria-label="Search"><circle cx="6.5" cy="6.5" r="4.5" fill="none" stroke="#1c1c1c" stroke-width="2"/><line x1="10" y1="10" x2="14.5" y2="14.5" stroke="#1c1c1c" stroke-width="2.4"/></svg>
  </nav>
</header>

<section class="hero" role="img" aria-label="Glowing blue hexagon grid of technology icons">
  <svg class="arrow" style="left:44px" width="18" height="32" viewBox="0 0 18 32"><polyline points="15,2 3,16 15,30" fill="none" stroke="#fff" stroke-width="3"/></svg>
  <svg class="arrow" style="right:44px" width="18" height="32" viewBox="0 0 18 32"><polyline points="3,2 15,16 3,30" fill="none" stroke="#fff" stroke-width="3"/></svg>
  <div class="hero-title line1">IT'S NOT ROCKET SCIENCE,</div>
  <div class="hero-title line2">IT'S FERNQUILL MEDIA SCIENCE!</div>
  <svg class="down" width="40" height="60" viewBox="0 0 40 60"><rect x="2" y="2" width="36" height="56" rx="18" fill="none" stroke="#fff" stroke-width="2"/><polyline points="12,26 20,34 28,26" fill="none" stroke="#fff" stroke-width="2.5"/></svg>
</section>

<section class="features">
  <div class="feature" style="left:83px">
    <svg width="70" height="70" viewBox="0 0 70 70"><rect x="6" y="12" width="58" height="40" rx="3" fill="none" stroke="#1a64ae" stroke-width="4"/><rect x="28" y="52" width="14" height="8" fill="#1a64ae"/><rect x="20" y="60" width="30" height="4" fill="#1a64ae"/><rect x="38" y="34" width="5" height="12" fill="#1a64ae"/><rect x="46" y="28" width="5" height="18" fill="#1a64ae"/><rect x="54" y="22" width="5" height="24" fill="#1a64ae"/><path d="M22 32 L22 20 A12 12 0 0 1 34 32 Z" fill="#1a64ae"/><circle cx="22" cy="32" r="10" fill="none" stroke="#1a64ae" stroke-width="3"/></svg>
    <h3>ANALYSIS</h3>
    <p>At vero eos et accusamus et iusto odi<br>o dignissimos ducimus qui</p>
  </div>
  <div class="feature" style="left:357px">
    <svg width="76" height="70" viewBox="0 0 76 70"><g stroke="#1a64ae" stroke-width="2" fill="none"><line x1="38" y1="30" x2="10" y2="14"/><line x1="38" y1="30" x2="38" y2="6"/><line x1="38" y1="30" x2="66" y2="14"/><line x1="38" y1="30" x2="8" y2="42"/><line x1="38" y1="30" x2="68" y2="42"/><line x1="10" y1="14" x2="38" y2="6"/><line x1="38" y1="6" x2="66" y2="14"/></g><g fill="#1a64ae"><circle cx="10" cy="14" r="5"/><circle cx="38" cy="6" r="5"/><circle cx="66" cy="14" r="5"/><circle cx="8" cy="42" r="5"/><circle cx="68" cy="42" r="5"/><circle cx="38" cy="34" r="8"/><path d="M22 66 Q22 46 38 46 Q54 46 54 66 Z"/></g></svg>
    <h3>TRULY GLOBAL</h3>
    <p>At vero eos et accusamus et iusto odi<br>o dignissimos ducimus qui</p>
  </div>
  <div class="feature" style="left:628px">
    <svg width="70" height="70" viewBox="0 0 70 70"><g fill="#1a64ae"><path d="M14 30 V20 A14 14 0 0 1 42 20 V30 H35 V20 A7 7 0 0 0 21 20 V30 Z"/><rect x="8" y="30" width="40" height="34" rx="4"/></g><circle cx="28" cy="44" r="4" fill="#fff"/><rect x="26" y="46" width="4" height="9" fill="#fff"/><g fill="#1a64ae"><circle cx="52" cy="44" r="8"/><rect x="50" y="50" width="4" height="16"/><rect x="54" y="58" width="6" height="3"/></g></svg>
    <h3>SAFER AND PROTECTED</h3>
    <p>At vero eos et accusamus et iusto odi<br>o dignissimos ducimus qui</p>
  </div>
  <div class="feature" style="left:877px">
    <svg width="70" height="70" viewBox="0 0 70 70"><circle cx="35" cy="32" r="26" fill="none" stroke="#1a64ae" stroke-width="4"/><path d="M18 52 L12 64 L28 56" fill="#1a64ae"/><text x="35" y="40" text-anchor="middle" font-family="Arimo, sans-serif" font-weight="700" font-size="20" fill="#1a64ae">24h</text></svg>
    <h3>CUSTOMER SUPPORT</h3>
    <p>At vero eos et accusamus et iusto odi<br>o dignissimos ducimus qui</p>
  </div>
</section>

<section class="welcome">
  <h2>WELCOME TO FERNQUILL MEDIA</h2>
  <div class="sub">Search Engine Optimization has been replaced with Search Experience Optimization</div>
  <p class="intro">SALES is the end result of everything we do. It is why companies exists. It's why we market. It's why your business is online. Our job is to help you maximize your opportunity online to build your brand, get found by new customers and, ultimately, generate SALES! There's been a lot of talk the last few years about SEO, Search Engine Optimization. <a class="readmore" href="#">READ MORE &gt;&gt;</a></p>

  <div class="stat" style="left:98px;top:240px">
    <div class="dot" style="background:var(--green)"><svg width="40" height="30" viewBox="0 0 40 30"><rect x="7" y="3" width="26" height="18" rx="2" fill="none" stroke="#fff" stroke-width="3"/><rect x="2" y="22" width="36" height="4" rx="1" fill="#fff"/></svg></div>
    <div class="num">93%</div>
    <p>Online experiences begin with a search engine</p>
  </div>
  <div class="stat" style="left:424px;top:240px">
    <div class="dot" style="background:var(--orange)"><svg width="40" height="32" viewBox="0 0 40 32"><g fill="#fff"><circle cx="20" cy="9" r="6"/><circle cx="8" cy="12" r="4"/><circle cx="32" cy="12" r="4"/><path d="M10 30 Q10 17 20 17 Q30 17 30 30 Z"/><path d="M1 28 Q1 18 8 18 Q11 18 12 20 Q9 24 9 28 Z"/><path d="M39 28 Q39 18 32 18 Q29 18 28 20 Q31 24 31 28 Z"/></g></svg></div>
    <div class="num">70%</div>
    <p>Of US population has at least one social networking profile</p>
  </div>
  <div class="stat" style="left:98px;top:354px">
    <div class="dot" style="background:var(--yellow)"><svg width="36" height="36" viewBox="0 0 36 36"><circle cx="14" cy="14" r="9" fill="none" stroke="#fff" stroke-width="4"/><line x1="21" y1="21" x2="32" y2="32" stroke="#fff" stroke-width="5" stroke-linecap="round"/></svg></div>
    <div class="num">70%</div>
    <p>Of the links search users click on are organic</p>
  </div>
  <div class="stat" style="left:424px;top:354px">
    <div class="dot" style="background:var(--cyan)"><svg width="40" height="36" viewBox="0 0 40 36"><g fill="none" stroke="#fff"><circle cx="15" cy="20" r="8" stroke-width="6" stroke-dasharray="4 2.3"/><circle cx="15" cy="20" r="3" stroke-width="2"/><circle cx="31" cy="9" r="5" stroke-width="4" stroke-dasharray="3 1.7"/></g></svg></div>
    <div class="num">50%</div>
    <p>Of companies are using digital marketing but don't have a plan</p>
  </div>

  <div class="phone-shot" role="img" aria-label="Hand holding a smartphone showing the brand on screen"></div>
</section>

<section class="facts">
  <h2>SOME FACTS ABOUT OUR CATALYSTS</h2>
  <div class="sub">Working together to create change</div>
  <div class="fact" style="left:116px"><div class="ring">35</div><p>Years Combined Marketing<br>Experience</p></div>
  <div class="fact" style="left:367px"><div class="ring">10</div><p>Years Search Engine Optimization<br>Experience</p></div>
  <div class="fact" style="left:615px"><div class="ring">234</div><p>Websites created</p></div>
  <div class="fact" style="left:864px"><div class="ring">1</div><p>Amazing team</p></div>
</section>

<section class="snapshot">
  <h2>LET US PUT TOGETHER AN OBJECTIVE SNAPSHOT OF YOUR DIGITAL PRESENCE FOR YOU</h2>
  <div class="copy">
    <p>We thrive on data. It's digital quantum mechanics! We immerse ourselves in metrics, analytics, and insights to continually improve each marketing initiative. We are nimble and can respond quickly to opportunities we see in the data. There is no room for complacency online!</p>
    <p>We optimize for the users search experience which makes logical sense and now is "rewarded" by Searchly and the other search engines.</p>
  </div>
  <a class="readmore" href="#">READ MORE &gt;&gt;</a>

  <svg class="abs" style="left:680px;top:40px" width="460" height="380" viewBox="680 40 460 380">
    <circle cx="920" cy="220" r="160" fill="none" stroke="#cfcfcf" stroke-width="2" stroke-dasharray="6 6"/>
    <circle cx="790" cy="134" r="36" fill="var(--green)"/>
    <rect x="779" y="114" width="22" height="38" rx="3" fill="none" stroke="#fff" stroke-width="3"/><circle cx="790" cy="146" r="2" fill="#fff"/>
    <circle cx="955" cy="80" r="36" fill="var(--coral)"/>
    <rect x="938" y="69" width="24" height="22" rx="3" fill="#fff"/><path d="M962 80 L975 70 V90 Z" fill="#fff"/>
    <circle cx="1060" cy="207" r="36" fill="var(--orange)"/>
    <rect x="1043" y="193" width="34" height="24" rx="2" fill="none" stroke="#fff" stroke-width="3"/><rect x="1056" y="217" width="8" height="5" fill="#fff"/><rect x="1050" y="222" width="20" height="3" fill="#fff"/>
    <circle cx="959" cy="356" r="36" fill="var(--cyan)"/>
    <path d="M947 338 H966 L973 345 V374 H947 Z" fill="none" stroke="#fff" stroke-width="3"/><line x1="952" y1="352" x2="968" y2="352" stroke="#fff" stroke-width="2"/><line x1="952" y1="359" x2="968" y2="359" stroke="#fff" stroke-width="2"/><line x1="952" y1="366" x2="968" y2="366" stroke="#fff" stroke-width="2"/>
    <circle cx="790" cy="289" r="36" fill="var(--yellow)"/>
    <path d="M774 282 H782 L800 270 V308 L782 296 H774 Z" fill="#fff"/><rect x="778" y="296" width="6" height="12" fill="#fff"/>
  </svg>
  <div class="cycle-label" style="left:734px;top:56px">MOBILE<br>FRIENDLINESS</div>
  <div class="cycle-label" style="left:1010px;top:60px">SOCIAL MEDIA<br>PRESENCE</div>
  <div class="cycle-label" style="left:1058px;top:252px">WEBSITE</div>
  <div class="cycle-label" style="left:1006px;top:355px">CONTENT</div>
  <div class="cycle-label" style="left:694px;top:206px">DIGITAL MEDIA<br>ADVERTISING</div>
</section>

<section class="prism" role="img" aria-label="Chemical structure diagram on a warm textured backdrop">
  <h2>FREE ONLINE PRISM CHECK</h2>
  <p>At vero eos et accusamus et iusto odio dignissimos ducimus qui blanditiis praesentium voluptatum deleniti atque corrupti quos dolores et quas molestias excepturi sint occaecati cupiditate non provident</p>
  <a class="btn" href="#">GET MORE INFO &gt;&gt;</a>
</section>

<section class="blog">
  <h2>OUR BLOG</h2>
  <svg class="side" style="left:70px" width="14" height="26" viewBox="0 0 14 26"><polyline points="12,2 2,13 12,24" fill="none" stroke="#bbb" stroke-width="2"/></svg>
  <svg class="side" style="right:70px" width="14" height="26" viewBox="0 0 14 26"><polyline points="2,2 12,13 2,24" fill="none" stroke="#bbb" stroke-width="2"/></svg>

  <article class="post" style="left:98px">
    <div class="thumb" role="img" aria-label="Cartoon blue bird with a caption ribbon" style="background:linear-gradient(180deg,#f3f3f3 0%,#e6eef6 60%,#9cc7e4 100%)"></div>
    <h3>A LITTLE BIRD TOLD ME – 5 REASONS FOR TWEETING</h3>
    <div class="meta">May 14, 2016 &nbsp;|&nbsp; 12:41</div>
    <p class="excerpt">There's a thin red line between social media use and networking. Sometimes the two merge into a perfect harmony of conversation and resolution.</p>
    <a class="readmore" href="#">READ MORE &gt;&gt;</a>
  </article>
  <article class="post" style="left:443px">
    <div class="thumb" role="img" aria-label="Dark corridor with the headline the revolution will now be optimized" style="background:linear-gradient(180deg,#2a2a2a 0%,#3c3c3c 50%,#1c1c1c 100%)"></div>
    <h3>THE REVOLUTION WILL NOW BE<br>OPTIMIZED</h3>
    <div class="meta">May 3, 2016 &nbsp;|&nbsp; 15:41</div>
    <p class="excerpt">With the advancement of technology, the Internet, and search engines, companies have sought to provide end-users an optimal..</p>
    <a class="readmore" href="#">READ MORE &gt;&gt;</a>
  </article>
  <article class="post" style="left:788px">
    <div class="thumb" role="img" aria-label="Chalkboard with the need for speed heading and a loading spinner" style="background:linear-gradient(180deg,#3a3d3c 0%,#2c2f2e 100%)"></div>
    <h3>SEARCHLY'S FAST TECH ENCOURAGES<br>NEW STANDARD FOR MOBILE PLATFORMS</h3>
    <div class="meta">April 15, 2016 &nbsp;|&nbsp; 15:41</div>
    <p class="excerpt">Do you ever feel frustrated waiting for pages to load on your phone? You are not the only one. Let's face it, we're an impatient bunch when..</p>
    <a class="readmore" href="#">READ MORE &gt;&gt;</a>
  </article>
</section>

<section class="contact">
  <h2>CONTACT US</h2>
  <h4 style="left:98px">CONTACT FORM</h4>
  <div class="field" style="left:98px;top:133px;width:310px">NAME :</div>
  <div class="field" style="left:422px;top:133px;width:306px">PHONE :</div>
  <div class="field" style="left:98px;top:175px;width:630px">EMAIL :</div>
  <div class="field" style="left:98px;top:217px;width:630px;height:62px">MESSAGE :</div>
  <div class="submit">SUBMIT</div>

  <h4 style="left:786px">CONTACT INFORMATION</h4>
  <div class="info" style="top:126px">
    <span class="ic"><svg width="14" height="18" viewBox="0 0 14 18"><path d="M7 1 A6 6 0 0 1 13 7 C13 11 7 17 7 17 C7 17 1 11 1 7 A6 6 0 0 1 7 1 Z" fill="#fff"/><circle cx="7" cy="7" r="2.2" fill="#0f2340"/></svg></span>
    <span>2870 W. Orchard Avenue<br>Suite 210<br>Brookhaven, TX 75410</span>
  </div>
  <div class="info" style="top:200px">
    <span class="ic"><svg width="18" height="14" viewBox="0 0 18 14"><rect x="1" y="1" width="16" height="12" rx="2" fill="#fff"/><polyline points="2,2 9,8 16,2" fill="none" stroke="#0f2340" stroke-width="1.6"/></svg></span>
    <span style="padding-top:8px">info@fernquillmedia.marketing</span>
  </div>
  <div class="info" style="top:252px">
    <span class="ic"><svg width="16" height="16" viewBox="0 0 16 16"><path d="M3 1 L6 1 L7 5 L5 6.5 Q6.5 9.5 9.5 11 L11 9 L15 10 L15 13 Q15 15 13 15 Q1 14 1 3 Q1 1 3 1 Z" fill="#fff"/></svg></span>
    <span style="padding-top:10px">555-014-2290</span>
  </div>
  <div class="socials" aria-label="Social profiles"><span></span><span></span><span></span><span></span></div>
</section>

<footer class="site-footer">© 2016, Fernquillmedia. All Rights Reserved.</footer>

</body>
</html>
```